New, modern business card for growing audiology practice

We need a new business card for our audiology practice. Our logo and website have recently changed (more modern) and we want our business cards to reflect this change.
We conduct hearing tests, perform earwax removals, and fit & dispense hearing aids to our patients. We are a family owned practice in which the owner is the one who works directly with the patient. I have attached logos in various formats to use, as well as two ideas I found on this website; as well as a scanned copy of our current logo. Good luck!

Industry/Entity Type

Business

Contact Information for Business Card

Company name: Tolvera Hearing Center
Provider name: Peter Wolstenby, Au.D. F/NSB
Phone number: (440) 683-5127
Address: 837 W. Lindell Ave. Brookmere Falls, OH 44917
email: tolverahearing@postvane.com
website: tolverahearing.com

Colors
000000
aaaaaa
dbdbdb
cacaca
9bcb3c
afd23c
cadf82
b1b1b1

Requirements
Must have
• My card must include information in the "details" section. In the attached images, I found a few that I liked and I would like to model after - "brisky bouncin'" and "Sound Method Center".
• Must be horizontal.
• Must include logos provided. I uploaded them in various file formats and various ways.
• Must match logo font, if possible, if not, please get as close as you can.
Nice to have
• I really like the idea of having a color on one side with just the logo and company name and the contact information and provider name on the other side. I also really like the idea of having the main color dominating on the logo/company side with accent of that same color on the contact side of the card.
Should not have
• Must not be vertical.

```html
<!DOCTYPE html>
<html lang="en">
<head>
<meta charset="utf-8">
<title>Tolvera Hearing Center – Business Card</title>
<link rel="stylesheet" href="https://fonts.googleapis.com/css2?family=Roboto:wght@400;500&family=Roboto+Condensed:wght@700&display=swap">
<style>
  :root {
    --stage: #e4e4e2;
    --paper: #f4f4f3;
    --ink: #161616;
    --green: #72a135;
    --green-light: #9bcb3c;
    --back: #1c1e20;
    --white: #ffffff;
  }
  * { box-sizing: border-box; margin: 0; padding: 0; }
  html, body { width: 1200px; height: 960px; overflow: hidden; }
  body {
    background: var(--stage);
    font-family: "Roboto", Arial, sans-serif;
    position: relative;
  }
  .card {
    position: absolute;
    width: 600px;
    height: 342px;
    border-radius: 22px;
    overflow: hidden;
    box-shadow: 0 3px 8px rgba(0,0,0,0.25);
  }
  .card--front { left: 314px; top: 113px; background: var(--paper); }
  .card--back { left: 311px; top: 472px; background: var(--back); }

  .brand {
    position: absolute;
    top: 60px;
    left: 0; right: 0;
    display: flex;
    justify-content: center;
    align-items: center;
    gap: 10px;
    font-weight: 400;
    font-size: 22px;
    letter-spacing: 0.3px;
    color: var(--ink);
    text-transform: uppercase;
  }
  .brand__dot {
    width: 14px; height: 14px;
    border-radius: 50%;
    background: var(--green);
  }
  .wave { position: absolute; left: 0; top: 0; }

  .provider {
    position: absolute;
    left: 41px; top: 245px;
    color: var(--white);
  }
  .provider__name {
    font-family: "Roboto Condensed", "Arial Narrow", sans-serif;
    font-weight: 700;
    font-size: 21px;
    letter-spacing: 0.2px;
  }
  .provider__title { font-size: 15px; font-weight: 500; margin-top: 3px; }

  .contact {
    position: absolute;
    left: 352px; top: 214px;
    color: var(--white);
    font-size: 14.5px;
    line-height: 19px;
  }
  .contact__address { margin-bottom: 10px; }
  .contact__row { display: flex; align-items: center; gap: 9px; height: 19.5px; }
  .contact__icon { width: 13px; height: 13px; flex: none; }

  .back-brand {
    position: absolute;
    top: 142px; left: 0; right: 0;
    display: flex;
    justify-content: center;
    align-items: center;
    gap: 14px;
    font-weight: 500;
    font-size: 30px;
    color: var(--green);
    text-transform: uppercase;
    letter-spacing: 1px;
  }
  .back-brand__dot {
    width: 26px; height: 26px;
    border-radius: 50%;
    background: var(--green);
  }
  .back-web {
    position: absolute;
    top: 294px; left: 0; right: 0;
    text-align: center;
    color: var(--white);
    font-size: 14px;
    letter-spacing: 4.3px;
  }
</style>
</head>
<body>
  <section class="card card--front">
    <div class="brand"><span class="brand__dot"></span><span>Tolvera Hearing Center</span></div>
    <svg class="wave" width="600" height="342" viewBox="0 0 600 342">
      <path d="M0 150 C50 205 170 215 330 178 S540 140 600 168 L600 190 C540 165 470 168 330 192 S60 212 0 165 Z" fill="var(--ink)"/>
      <path d="M0 162 C60 212 190 215 330 188 S545 158 600 195 L600 342 L0 342 Z" fill="var(--green)"/>
      <path d="M20 185 C90 215 210 214 330 192 S540 162 600 200" fill="none" stroke="var(--white)" stroke-width="2.5"/>
    </svg>

    <div class="provider">
      <div class="provider__name">PETER WOLSTENBY</div>
      <div class="provider__title">AU.D. F/NSB</div>
    </div>

    <div class="contact">
      <div class="contact__address">837 W. Lindell Ave.<br>Brookmere Falls, OH 44917</div>
      <div class="contact__row">
        <svg class="contact__icon" viewBox="0 0 24 24"><path fill="#fff" d="M6.6 10.8a15 15 0 0 0 6.6 6.6l2.2-2.2c.3-.3.7-.4 1-.2 1.1.4 2.3.6 3.6.6.6 0 1 .4 1 1V20c0 .6-.4 1-1 1A17 17 0 0 1 3 4c0-.6.4-1 1-1h3.5c.6 0 1 .4 1 1 0 1.3.2 2.5.6 3.6.1.3 0 .7-.2 1z"/></svg>
        <span>(440) 683-5127</span>
      </div>
      <div class="contact__row">
        <svg class="contact__icon" viewBox="0 0 24 24"><path fill="#fff" d="M2 5h20v14H2z"/><path fill="none" stroke="#72a135" stroke-width="2" d="M2 6l10 7 10-7"/></svg>
        <span>tolverahearing@postvane.com</span>
      </div>
      <div class="contact__row">
        <svg class="contact__icon" viewBox="0 0 24 24"><circle cx="12" cy="12" r="10" fill="#fff"/><path fill="none" stroke="#72a135" stroke-width="1.6" d="M2 12h20M12 2c3 3 3 17 0 20M12 2c-3 3-3 17 0 20"/></svg>
        <span>www.tolverahearing.com</span>
      </div>
    </div>
  </section>

  <section class="card card--back">
    <div class="back-brand"><span class="back-brand__dot"></span><span>Tolvera</span></div>
    <div class="back-web">www.tolverahearing.com</div>
  </section>
</body>
</html>
```